KorvaNest - Home Income and Business Resources Platform

I am looking for a website template for a multi-purposed website. This website will feature:

1.) Website Directory with Ratings & comments on listings
2.) Company Blog
3.) Homepage with Content (see files for homepage mock)

I would like the Design to have a default width 1170px (wider then normal)

Of course I am looking for Pages for Listings to be designed.

Great looking BLOG Layout: http://journal.plimworks.example/html/blog.html

I would like 4 Versions of a Website Directory Listing "Box"
1.) Basic Listing Box
2.) Sponsored Listing Box
3.) Recommended Listing Box
4.) Stay Away From Listing Box

Information on the Listing Page (Like on a Category Page)
Site Name, Site URL, Website Image, # of Views, Rating and # of Comments

Information on the Listing Details Page:
Same as ABOVE + About website Description, Vornic Score, Category Information

Decent looking examples is here: https://samples.trevolin.example/directory/computers/ and http://www.zqrankhub.example/.

I will include some sketches and screenshots of things I like/looking for. As designers,you have creative freedom and are encouraged to show this. This is Phase one of this project and winning designer is guaranteed to have future work for this project.

Target Market(s)

Directory, business, websites

Industry/Entity Type

Business

Coding

Coded - Design and coding required

Number of Pages Required

5+ page

Font styles to use
Sans Serif

Colors

Designer to choose colors to be used in the design.

Requirements
Must have
• Professional yet clean look. The use of Icons & images
• Unique Look
Should not have
• Any exact copies of any examples I provided

```html
<!DOCTYPE html>
<html lang="en">
<head>
<meta charset="utf-8">
<title>KorvaNest – About</title>
<link rel="stylesheet" href="https://fonts.googleapis.com/css2?family=Roboto:wght@400&family=Roboto+Condensed:wght@400;700&family=Open+Sans:wght@400;600&display=swap">
<style>
:root{
  --brand:#2f74cf;
  --page:#ececec;
  --panel:#f7f7f7;
  --card:#ffffff;
  --line:#d6d6d6;
  --ink:#222222;
  --text:#555555;
  --footer:#161616;
  --white:#ffffff;
}
*{box-sizing:border-box;margin:0;padding:0}
html,body{width:1200px;height:1051px;overflow:hidden}
body{position:relative;background:var(--page);font-family:"Open Sans",sans-serif;color:var(--text)}
.site-header{position:absolute;left:0;top:0;width:1200px;height:77px;background:var(--brand)}
.brand-name{position:absolute;left:96px;top:18px;font-family:"Roboto Condensed",sans-serif;font-weight:700;font-size:38px;line-height:1;color:var(--white);letter-spacing:.5px}
.main-nav{position:absolute;top:29px;left:556px;display:flex}
.main-nav a{font-family:"Roboto",sans-serif;font-size:16px;color:var(--white);text-decoration:none;margin-right:61px}
.main-nav a:last-child{margin-right:0}
.content-panel{position:absolute;left:74px;top:77px;width:1054px;height:803px;background:var(--panel);box-shadow:0 0 3px rgba(0,0,0,.06)}
.about-box{position:absolute;left:100px;top:143px;width:774px;height:296px;border:1px solid var(--line);background:linear-gradient(90deg,#ffffff 0%,#fbfbfc 45%,#eef0f4 100%);overflow:hidden}
.about-photo{position:absolute;right:0;top:0;width:430px;height:100%;background:radial-gradient(ellipse at 55% 35%,rgba(230,200,180,.45),rgba(200,210,225,.35) 55%,rgba(255,255,255,0) 80%)}
.about-box h1{position:absolute;left:41px;top:54px;font-family:"Roboto Condensed",sans-serif;font-weight:400;font-size:30px;color:var(--brand)}
.about-box p{position:absolute;left:41px;top:111px;width:672px;font-size:14px;line-height:25.4px;text-align:justify;color:#444}
.feature-card{position:absolute;top:460px;width:251px;height:336px;background:var(--card);border:1px solid var(--line);text-align:center}
.feature-card.home{left:100px}.feature-card.ads{left:361px}.feature-card.earn{left:622px}
.feature-icon{display:block;width:52px;height:52px;margin:28px auto 0;border-radius:6px}
.home .feature-icon{background:linear-gradient(135deg,#f0b429,#2e9e5b)}
.ads .feature-icon{background:linear-gradient(135deg,#f05a28,#9fb4cc)}
.earn .feature-icon{background:linear-gradient(135deg,#f5b82e,#3a70c9)}
.feature-card h2{font-family:"Roboto Condensed",sans-serif;font-weight:400;font-size:15.5px;line-height:22px;color:var(--ink);margin:12px 18px 0;padding-bottom:9px;border-bottom:1px solid var(--line);height:54px}
.feature-card p{font-size:10.6px;line-height:16.7px;margin:15px 24px 0;text-align:justify;text-align-last:center}
.sponsor-box{position:absolute;left:886px;top:141px;width:218px;height:201px;background:var(--card);border:1px solid var(--line);text-align:center}
.sponsor-box h3{font-family:"Roboto Condensed",sans-serif;font-weight:400;font-size:21px;color:var(--brand);margin-top:20px}
.sponsor-list{list-style:none;margin-top:10px}
.sponsor-list li{display:flex;align-items:center;justify-content:center;gap:7px;height:41px;font-weight:600;font-size:20px;color:#7d7d7d}
.sponsor-list li::before{content:"";width:15px;height:15px;border-radius:50%;background:#9a9a9a}
.ad-slot{position:absolute;left:886px;width:219px;height:219px}
.ad-slot.app{top:351px;background:linear-gradient(160deg,#3b8fe0 0%,#2b6fd0 55%,#dfeffc 100%)}
.ad-slot.design{top:576px;background:linear-gradient(180deg,#5fb0c8 0%,#1fa5b0 45%,#1e4fa0 100%)}
.site-footer{position:absolute;left:0;top:880px;width:1200px;height:171px;background:var(--footer);color:var(--white);text-align:center}
.footer-nav{margin-top:45px;font-size:13px}
.footer-nav a{color:var(--white);text-decoration:none;margin:0 9px}
.social-list{display:flex;justify-content:center;gap:8px;margin-top:13px}
.social-list li{list-style:none;width:26px;height:26px;border:1.5px solid #8a8a8a;border-radius:50%;display:flex;align-items:center;justify-content:center}
.copyright{margin-top:10px;font-size:13px}
</style>
</head>
<body>
<header class="site-header">
  <div class="brand-name">Korva Nest</div>
  <nav class="main-nav">
    <a href="#">HOME</a><a href="#">ABOUT US</a><a href="#">SERVICES</a><a href="#">BLOG</a><a href="#">CONTACTS</a>
  </nav>
</header>

<main class="content-panel"></main>

<section class="about-box">
  <div class="about-photo" role="img" aria-label="Faint photo of a businessman holding a tablet over a city skyline"></div>
  <h1>ABOUT KORVANEST</h1>
  <p>It is a long established fact that a reader will be distracted by the readable content of a page when looking at its layout. The point of using Lorem Ipsum is that it has a more-or-less normal distribution of letters, as opposed to using 'Content here, content here', making it look like readable English. Many desktop publishing packages and web page editors now use Lorem Ipsum as their default model text, and a search for 'lorem ipsum' will uncover many web sites still in their infancy. Various versions have evolved over the years, sometimes by accident, sometimes on purpose</p>
</section>

<article class="feature-card home">
  <span class="feature-icon" role="img" aria-label="Icon of gold coins and a banknote"></span>
  <h2>HOME INCOME<br>RESOURCE DIRECTORY</h2>
  <p>Find what you need, when you need it.The KorvaNest website directory is your one-stop pit for anything involved in making money from home, marketing your business or finding a new opportunity. Our modern, community supported directory will help you keep upto todate with the lastest information in a sensible fashion</p>
</article>
<article class="feature-card ads">
  <span class="feature-icon" role="img" aria-label="Icon of a megaphone"></span>
  <h2>ADVERTISING<br>BENEFITS</h2>
  <p>Everyone needs to advertise and we know just how to get your offer out to the right people. We have many methods including: Text ads, E-mail, Display, newsletter and even some old school methods available to make your next campaign a success. Advertise a website, a link text, full page circular or a small display ad and get results.</p>
</article>
<article class="feature-card earn">
  <span class="feature-icon" role="img" aria-label="Icon of a hand holding a dollar coin"></span>
  <h2>EARNING WITH<br>KORVANEST</h2>
  <p>Join KorvaNest and start earning money. When you share KorvaNest and lock in an advertiser or premium listing, we reward you. Build a downline at any of our listed sites when you share KorvaNest with NO extra work. Its all done for you.We also offer a revenue share program for true supporters of our mission.</p>
</article>

<aside class="sponsor-box">
  <h3>SPONSORED</h3>
  <ul class="sponsor-list">
    <li>Quellix</li>
    <li>Durvane</li>
    <li>Magmora</li>
  </ul>
</aside>

<aside class="ad-slot app" role="img" aria-label="Banner advert for a cloud business app with a tablet and phone among clouds"></aside>
<aside class="ad-slot design" role="img" aria-label="Banner advert for web design services with a colourful umbrella and signpost"></aside>

<footer class="site-footer">
  <nav class="footer-nav">
    <a href="#">ABOUT</a><span>|</span><a href="#">PRIVACY</a><span>|</span><a href="#">TERMS</a><span>|</span><a href="#">LEGAL</a><span>|</span><a href="#">CONTACT</a>
  </nav>
  <ul class="social-list">
    <li></li><li></li><li></li><li></li><li></li>
    <li><svg width="12" height="10" viewBox="0 0 12 10"><rect x="0.75" y="0.75" width="10.5" height="8.5" rx="1" fill="none" stroke="#bbb" stroke-width="1.2"/><path d="M1 1.5 6 5.5 11 1.5" fill="none" stroke="#bbb" stroke-width="1.2"/></svg></li>
  </ul>
  <p class="copyright">Copyright © 2017&nbsp; All Rights Reserved</p>
</footer>
</body>
</html>
```